Animal Eye Clinic needs a Business card

We are a new veterinary ophthalmology practice (Ridgeline Pet Vision Care) and we need a business card designed. We only see animal eyes - we are not a regular veterinary clinic. We already have a logo. We are looking for a professional, good looking business card to hand out to our clients. We are looking for something simple but professional and contemporary. Our logo is likely the only picture/graphic that needs to be on the card.
Updates

Contact Information for Business Card

Delia Vossman, BSc, DVM, MSc, DipACVO
Veterinary Ophthalmologist

Phone: 250.418.3927
Email: ridgelinepetvisioncare@mailbox-example.net
Website: ridgelinepetvisioncare-example.net
Address: 1874 Thornbury Rd
Kelowna, BC, V1X 4M9

Colors

Designer to choose colors to be used in the design.

Requirements
Must have
• Our logo (attached)

```html
<!DOCTYPE html>
<html lang="en">
<head>
<meta charset="utf-8">
<title>Ridgeline Pet Vision Care – Business Card</title>
<link href="https://fonts.googleapis.com/css2?family=Lato:wght@400;700;900&display=swap" rel="stylesheet">
<style>
  :root {
    --teal: #1a9aa8;
    --teal-dark: #12808c;
    --name-blue: #2a8fc9;
    --ink: #2b2b2b;
    --grey-band: #3a3a3a;
    --paper: #fbfbfb;
    --backdrop: #2c2c2c;
  }
  * { margin: 0; padding: 0; box-sizing: border-box; }
  html, body {
    width: 1200px; height: 997px; overflow: hidden;
    background: var(--backdrop);
    font-family: "Lato", Arial, sans-serif;
  }
  .sheet {
    position: relative; width: 1200px; height: 997px;
    display: flex; flex-direction: column; align-items: center; justify-content: center; gap: 60px;
  }
  .card {
    position: relative; width: 700px; height: 400px; overflow: hidden;
    box-shadow: 0 12px 30px rgba(0,0,0,.5);
  }
  /* Front */
  .card--front {
    background: var(--teal);
    display: flex; align-items: center; justify-content: center; gap: 22px;
  }
  .brand-dot { width: 64px; height: 64px; border-radius: 50%; background: #fff; flex: none; }
  .brand-name { font-weight: 900; font-size: 38px; color: #fff; letter-spacing: .5px; }
  /* Back */
  .card--back { background: var(--paper); }
  .card__bands { position: absolute; inset: 0; }
  .back-brand {
    position: absolute; left: 60px; top: 48px;
    display: flex; align-items: center; gap: 18px;
  }
  .back-brand .brand-dot { width: 52px; height: 52px; background: var(--teal); }
  .back-brand .brand-name { color: var(--teal); font-size: 32px; }
  .rule { position: absolute; height: 2px; background: var(--name-blue); }
  .rule--top { left: 300px; right: 40px; top: 128px; }
  .person { position: absolute; left: 60px; top: 170px; }
  .person__name { font-weight: 700; font-size: 22px; color: var(--name-blue); letter-spacing: 1px; }
  .person__creds, .person__title { font-size: 15px; color: var(--ink); line-height: 1.25; }
  .rule--person { left: 60px; width: 260px; top: 240px; }
  .contacts { position: absolute; left: 60px; top: 258px; list-style: none; }
  .contacts li { display: flex; align-items: center; gap: 10px; font-size: 16px; color: var(--ink); margin-bottom: 8px; }
  .contacts svg { width: 18px; height: 18px; flex: none; }
  .address {
    position: absolute; right: 40px; top: 152px; text-align: right;
    font-size: 16px; color: var(--ink); line-height: 1.45;
  }
  .website {
    position: absolute; right: 30px; bottom: 32px;
    font-weight: 700; font-size: 15px; color: #fff; letter-spacing: .5px;
  }
</style>
</head>
<body>
<main class="sheet">
  <section class="card card--front" aria-label="Card front">
    <span class="brand-dot"></span>
    <span class="brand-name">Ridgeline Pet Vision Care</span>
  </section>

  <section class="card card--back" aria-label="Card back">
    <svg class="card__bands" viewBox="0 0 700 400" preserveAspectRatio="none" aria-hidden="true">
      <path d="M0 370 L330 330 Q345 328 340 340 L0 382 Z" fill="var(--grey-band)"/>
      <path d="M0 386 L700 386 L700 400 L0 400 Z" fill="var(--teal)"/>
      <path d="M400 332 Q410 318 440 316 L700 316 L700 386 L330 386 Q380 370 400 332 Z" fill="var(--teal)"/>
    </svg>

    <div class="back-brand">
      <span class="brand-dot"></span>
      <span class="brand-name">Ridgeline Pet Vision Care</span>
    </div>
    <div class="rule rule--top"></div>

    <div class="person">
      <p class="person__name">DELIA VOSSMAN</p>
      <p class="person__creds">BSc, DVM, MSc, DipACVO</p>
      <p class="person__title">Veterinary Ophthalmologist</p>
    </div>
    <div class="rule rule--person"></div>

    <ul class="contacts">
      <li>
        <svg viewBox="0 0 18 18"><circle cx="9" cy="9" r="9" fill="var(--name-blue)"/><path d="M6 5 L8 5 L8.6 7.2 L7.6 8 Q8.5 10 10 10.6 L10.8 9.6 L13 10.2 L13 12.2 Q9 12.8 6.5 10 Q5 8 6 5 Z" fill="#fff"/></svg>
        250.418.3927
      </li>
      <li>
        <svg viewBox="0 0 18 18"><circle cx="9" cy="9" r="9" fill="var(--name-blue)"/><rect x="4.5" y="6" width="9" height="6.5" fill="none" stroke="#fff" stroke-width="1.2"/><path d="M4.5 6 L9 9.6 L13.5 6" fill="none" stroke="#fff" stroke-width="1.2"/></svg>
        ridgelinepetvisioncare@mailbox-example.net
      </li>
    </ul>

    <address class="address" style="font-style:normal">
      1874 Thornbury Rd,<br>Kelowna, BC, V1X 4M9
    </address>
    <p class="website">www.ridgelinepetvisioncare-example.net</p>
  </section>
</main>
</body>
</html>
```